Private lender of mortgages and rent to own housing

need a website that reflects real estate especially mortgage lending and rent to own houses..
Sections as follows
Home About Types of mortgages Rent to own Contact us
Target Market(s)
consumers who require non traditonal mortgages
Industry/Entity Type
Mortgage
Coding
Coded - Design and coding required
Number of Pages Required
4 page
Font styles to use
Sans Serif
Colors
Designer to choose colors to be used in the design.
Requirements
Must have
- background pictures on pages. with nice picture on homepage of houses or a community
Nice to have
- contact us form i supplied a ink to

```html
<!DOCTYPE html>
<html lang="en">
<head>
<meta charset="utf-8">
<title>Lakeshore Lending Group</title>
<link rel="stylesheet" href="https://fonts.googleapis.com/css2?family=Open+Sans:ital,wght@0,300;0,400;0,600;0,700;1,400&family=Ubuntu:wght@300;500;700&display=swap">
<style>
:root{
  --navy:#25215e;
  --ink:#333;
  --muted:#8a8a8a;
  --hero:#5b7fb5;
  --rule:#1f4e9a;
  --dark:#2b2b2b;
  --btn-dark:#3a3a3a;
  --white:#fff;
}
*{margin:0;padding:0;box-sizing:border-box}
html,body{width:674px;height:1200px;overflow:hidden;background:var(--white)}
body{position:relative;font-family:"Open Sans",Arial,sans-serif;color:var(--ink)}
.abs{position:absolute}

/* header */
.site-header{position:absolute;left:0;top:0;width:674px;height:61px;background:var(--white);border-top:2px solid var(--navy);border-bottom:2px solid var(--rule)}
.brand{position:absolute;left:56px;top:34px;font-family:"Ubuntu",sans-serif;font-weight:700;font-size:9px;color:var(--navy);letter-spacing:.2px}
.main-nav{position:absolute;top:24px;left:0;font-size:6.5px;color:#666;letter-spacing:.3px}
.main-nav a{position:absolute;white-space:nowrap;text-decoration:none;color:inherit}
.main-nav a.active{color:var(--navy)}
.nav-mark{position:absolute;left:279px;top:36px}
.search-icon{position:absolute;left:611px;top:25px}

/* hero */
.hero{position:absolute;left:0;top:61px;width:674px;height:333px;background:linear-gradient(100deg,#4c6ea6 0%,#6c8fc3 45%,#5b7fb5 70%,#3f5f93 100%)}
.hero-title{position:absolute;left:54px;top:106px;color:var(--white);font-family:"Open Sans",sans-serif}
.hero-title .line1{display:block;font-size:37px;font-weight:700;letter-spacing:1px;line-height:40px}
.hero-title .line2{display:block;font-size:33px;font-weight:300;letter-spacing:.5px;line-height:44px}
.hero-dots{position:absolute;left:55px;top:210px;display:flex;gap:4px}
.hero-dots span{width:8px;height:8px;border-radius:50%;border:1.3px solid var(--white)}
.hero-dots span.on{border-color:#9ad0ff}

/* section headings */
.section-title{position:absolute;left:0;width:674px;text-align:center;font-family:"Ubuntu",sans-serif;font-weight:700;color:var(--navy);font-size:18.5px;letter-spacing:.4px}
.swoosh{position:absolute;left:314px}

/* rent to own */
.lead-sub{position:absolute;top:454px;width:674px;text-align:center;font-size:8.5px;color:#555}
.lead-copy{position:absolute;left:58px;top:499px;width:558px;text-align:center;font-size:6.6px;line-height:14.4px;color:#444}
.btn{position:absolute;display:flex;align-items:center;justify-content:center;gap:3px;color:var(--white);border-radius:3px;font-size:6.6px;text-decoration:none}
.btn-navy{background:var(--navy)}
.btn-dark{background:var(--btn-dark)}

/* process */
.process{position:absolute;left:0;top:633px;width:674px;height:275px;background:linear-gradient(90deg,#e4e0d8 0%,#efede6 30%,#e8e3da 60%,#ddd7cc 100%)}
.step{position:absolute;top:90px;width:124px;text-align:center}
.step h3{font-family:"Ubuntu",sans-serif;font-weight:500;font-size:10px;color:#333;letter-spacing:.3px;margin-top:4px}
.step.first h3{color:var(--navy)}
.step p{font-size:6.5px;line-height:12.6px;color:#333;margin:5px auto 0;width:98px;height:51px}

/* testimonials */
.testi-intro{position:absolute;left:96px;top:981px;width:482px;text-align:center;font-size:6.6px;line-height:14.4px;color:var(--muted);font-weight:300}
.testi-rule{position:absolute;left:190px;top:1020px;width:287px;height:1px;background:#e2e2e2}
.testi-rule i{position:absolute;left:141px;top:-2px;width:5px;height:5px;border-radius:50%;border:1px solid #ddd;background:var(--white)}
.avatar{position:absolute;width:62px;height:62px;border-radius:50%;border:2px solid #e6e6e6}
.quote{position:absolute;width:150px}
.quote .name{font-family:"Ubuntu",sans-serif;font-weight:500;font-size:6.2px;color:var(--navy)}
.quote .date{font-size:5.8px;color:#333;margin-top:3px}
.quote .body{font-size:6px;font-style:italic;line-height:12.5px;color:#777;margin-top:3px}
.slide-arrow{position:absolute;top:1067px;color:#ccc;font-size:12px;font-weight:300}

/* footer */
.site-footer{position:absolute;left:0;top:1142px;width:674px;height:58px;background:var(--dark)}
.footer-nav{position:absolute;left:56px;top:15px;font-size:6.2px;color:#ddd;white-space:nowrap}
.footer-nav span{color:#aaa;margin:0 4px}
.copyright{position:absolute;left:56px;top:31px;font-size:6px;color:#999}
.copyright b{font-weight:400;color:#ddd}
.connect{position:absolute;left:476px;top:24px;font-size:6.2px;color:#ddd}
.social{position:absolute;top:19px;width:16px;height:16px;border-radius:50%}
</style>
</head>
<body>

<header class="site-header">
  <div class="brand">LAKESHORE LENDING GROUP</div>
  <nav class="main-nav">
    <a class="active" style="left:279px">HOME</a>
    <a style="left:326px">ABOUT</a>
    <a style="left:376px">TYPES OF MORTGAGES</a>
    <a style="left:477px">RENT TO OWN</a>
    <a style="left:550px">CONTACT US</a>
  </nav>
  <svg class="nav-mark" width="22" height="4" viewBox="0 0 22 4"><path d="M1 3 Q11 -1 21 2" stroke="#25215e" stroke-width="1.3" fill="none"/></svg>
  <svg class="search-icon" width="8" height="8" viewBox="0 0 8 8"><circle cx="3.2" cy="3.2" r="2.4" stroke="#666" stroke-width="1.1" fill="none"/><path d="M5 5 L7.5 7.5" stroke="#666" stroke-width="1.2"/></svg>
</header>

<section class="hero" role="img" aria-label="Photo of a smiling couple signing home purchase papers">
  <h1 class="hero-title"><span class="line1">LAKESHORE</span><span class="line2">LENDING GROUP</span></h1>
  <div class="hero-dots"><span class="on"></span><span></span><span class="on"></span></div>
</section>
<svg class="abs" style="left:0;top:61px" width="674" height="370" viewBox="0 61 674 370">
  <circle cx="552" cy="144" r="66" fill="#fff" fill-opacity=".35"/>
  <circle cx="552" cy="144" r="53" fill="#8a7a6c" role="img" aria-label="Photo of a young couple at home"/>
  <circle cx="465" cy="239" r="53" fill="#fff" fill-opacity=".35"/>
  <circle cx="465" cy="239" r="42" fill="#c9c2b8" role="img" aria-label="Photo of a small model house in a hand"/>
  <circle cx="541" cy="352" r="78" fill="#fff" fill-opacity=".35"/>
  <circle cx="541" cy="352" r="63" fill="#c4a98a" role="img" aria-label="Photo of a house exterior with hands signing a contract"/>
</svg>

<h2 class="section-title" style="top:426px">RENT TO OWN A HOME</h2>
<p class="lead-sub">We Can Put You in Your Own Home Today</p>
<svg class="swoosh" style="top:476px" width="46" height="8" viewBox="0 0 46 8"><path d="M1 7 Q23 -2 45 3 Q23 1 1 7Z" fill="#25215e"/></svg>
<p class="lead-copy">We know life sometimes delivers challenges and it can be hard to get back on track once you have dealt with challenges. Maybe you have been through a divorce, bankruptcy, consumer proposal, loss of job, work place injury, new to the country, self-employed or some credit related challenges that have you behind the eight ball? Are these challenges making it difficult to get a mortgage? None of these things has to bind you to a lifetime of renting. Want to start paying yourself first? We focus on rent to own in Simcoe County and our Renting Program is a very viable option for those that can't get a mortgage today but are willing to work towards getting approved in the near future while living in their own home that they select. Homeownership is closer than you think.</p>
<a class="btn btn-navy" style="left:302px;top:587px;width:70px;height:23px;font-size:7px">READ MORE <b>»</b></a>

<section class="process" role="img" aria-label="Soft blurred photo of a bright living room">
  <h2 class="section-title" style="top:24px;color:var(--navy)">OUR PROCESS</h2>
  <svg class="swoosh" style="top:62px" width="46" height="8" viewBox="0 0 46 8"><path d="M1 7 Q23 -2 45 3 Q23 1 1 7Z" fill="#25215e"/></svg>

  <div class="step first" style="left:42px">
    <svg width="90" height="50" viewBox="0 0 90 50">
      <path d="M3 24 L45 1 L87 24 L45 7Z" fill="#25215e"/>
      <path d="M42 21 h6 v8 h4 l-7 7 l-7 -7 h4z" fill="#25215e"/>
      <rect x="33" y="39" width="24" height="6" rx="1" fill="#25215e"/>
      <circle cx="53" cy="42" r="1" fill="#fff"/>
    </svg>
    <h3>DOWN PAYMENT</h3>
    <p>We require a minimum down payment of $10,000 or 3.5% to 4% of total price of the home (whichever is larger).</p>
    <a class="btn btn-navy" style="position:relative;margin:7px auto 0;width:51px;height:18px">READ MORE <b>»</b></a>
  </div>

  <div class="step" style="left:197px">
    <svg width="90" height="50" viewBox="0 0 90 50">
      <path d="M3 24 L45 1 L87 24 L45 7Z" fill="#333"/>
      <circle cx="46" cy="28" r="6" fill="none" stroke="#333" stroke-width="1.3"/>
      <text x="46" y="31" font-size="8" text-anchor="middle" fill="#333" font-family="Open Sans,sans-serif">$</text>
      <path d="M32 40 q6 -6 12 -2 h6 q3 1 0 3 h-6 M50 40 l7 -4 q3 -1 2 2 l-8 7 h-14" fill="none" stroke="#333" stroke-width="1.3"/>
    </svg>
    <h3>HOUSEHOLD INCOME</h3>
    <p>Steady, provable household income that can support the price of the home you would like. A general guideline</p>
    <a class="btn btn-dark" style="position:relative;margin:7px auto 0;width:51px;height:18px">READ MORE <b>»</b></a>
  </div>

  <div class="step" style="left:351px">
    <svg width="90" height="50" viewBox="0 0 90 50">
      <path d="M3 24 L45 1 L87 24 L45 7Z" fill="#333"/>
      <rect x="35" y="29" width="20" height="15" rx="1.5" fill="none" stroke="#333" stroke-width="1.4"/>
      <rect x="35" y="33" width="20" height="3" fill="#333"/>
      <rect x="38" y="39" width="6" height="1.5" fill="#333"/>
    </svg>
    <h3>CREDIT REPORT</h3>
    <p>Although your credit won't necessarily disqualify you from our rent to own program, it is important improve</p>
    <a class="btn btn-dark" style="position:relative;margin:7px auto 0;width:51px;height:18px">READ MORE <b>»</b></a>
  </div>

  <div class="step" style="left:506px">
    <svg width="90" height="50" viewBox="0 0 90 50">
      <path d="M3 24 L45 1 L87 24 L45 7Z" fill="#333"/>
      <path d="M34 36 L45 26 L56 36 L53 36 L53 45 L48 45 L48 39 L42 39 L42 45 L37 45 L37 36Z" fill="#333"/>
    </svg>
    <h3>SELECTING A HOUSE</h3>
    <p>May not seem like a strong determining factor overall for qualifying for rent to own but it is for us.</p>
    <a class="btn btn-dark" style="position:relative;margin:7px auto 0;width:51px;height:18px">READ MORE <b>»</b></a>
  </div>
</section>

<h2 class="section-title" style="top:930px">TESTIMONIALS</h2>
<svg class="swoosh" style="top:959px" width="46" height="8" viewBox="0 0 46 8"><path d="M1 7 Q23 -2 45 3 Q23 1 1 7Z" fill="#25215e"/></svg>
<p class="testi-intro">On the other hand, we denounce with righteous indignation and dislike men who are so beguiled and demoralized by the charms of pleasure of the moment, so blinded by desire, that they cannot foresee the pain</p>
<div class="testi-rule"><i></i></div>

<span class="slide-arrow" style="left:86px">‹</span>
<div class="avatar" style="left:111px;top:1040px;background:#cdbfb2" role="img" aria-label="Portrait of a client"></div>
<div class="quote" style="left:190px;top:1049px">
  <div class="name">NEMO ENIM IPSAM</div>
  <div class="date">Posted on 06 Sep 2017</div>
  <div class="body">At vero eos et accusamus et iusto odio dignissi-mos ducimus qui praesentium..</div>
</div>
<div class="avatar" style="left:352px;top:1040px;background:#d8bfae" role="img" aria-label="Portrait of a client"></div>
<div class="quote" style="left:431px;top:1049px">
  <div class="name">NEMO ENIM IPSAM</div>
  <div class="date">Posted on 06 Sep 2017</div>
  <div class="body">At vero eos et accusamus et iusto odio dignissi-mos ducimus qui praesentium..</div>
</div>
<span class="slide-arrow" style="left:583px">›</span>

<footer class="site-footer">
  <div class="footer-nav">HOME<span>/</span>ABOUT<span>/</span>TYPES OF MORTGAGES<span>/</span>RENT TO OWN<span>/</span>CONTACT US</div>
  <div class="copyright">Copyright © 2017. <b>Lakeshore Lending.</b> All Right Resered</div>
  <div class="connect">CONNECT US :</div>
  <span class="social" style="left:522px;background:#3b5998"></span>
  <span class="social" style="left:542px;background:#2ba9e1"></span>
  <span class="social" style="left:562px;background:#dd4b39"></span>
  <span class="social" style="left:582px;background:#e2405a"></span>
  <span class="social" style="left:602px;background:#f2b01e"></span>
</footer>

</body>
</html>
```